New Innovative Counselling and psychotherapy Service needs Business Card design

Keep it simple and professional. On one side, just company name and logo (perhaps in all blue) and maybe a tag line.

On other side (all white) my name and Qualifications in centre

Industry/Entity Type

Health And Wellness

Contact Information for Business Card

Dara Whelby
Counsellor & Psychotherapist
BSc (Psychol.), BA, Dip. (Couns. & Psych.), PG.Cert (CBT), FGTrK, ONRE

I will also require Mobile no, Email and web site address of which I'll pass on to final designer.

Font styles to use
Sans Serif

Requirements
Must have
• My Logo Only and please use the colours in logo that is in it.
Should not have
• Any other images

```html
<!DOCTYPE html>
<html lang="en">
<head>
<meta charset="utf-8">
<title>Thrive Lane – Business Cards</title>
<link rel="stylesheet" href="https://fonts.googleapis.com/css2?family=Open+Sans:wght@400;700&display=swap">
<style>
  :root {
    --canvas-bg: #e9ebee;
    --card-white: #ffffff;
    --brand-blue: #45b3ec;
    --brand-sky: #5ec6f2;
    --ink-dark: #2f3337;
    --ink-grey: #6e7378;
    --on-blue: #ffffff;
    --divider: rgba(255,255,255,0.75);
  }
  * { box-sizing: border-box; margin: 0; padding: 0; }
  html, body {
    width: 1200px; height: 900px; overflow: hidden;
    background: var(--canvas-bg);
    font-family: "Open Sans", Arial, sans-serif;
  }
  .stage { position: relative; width: 1200px; height: 900px; }
  .card {
    position: absolute; left: 290px; width: 620px; height: 354px;
    background: var(--card-white);
    box-shadow: 0 6px 18px rgba(0,0,0,0.12);
    overflow: hidden;
  }
  .card--front { top: 66px; }
  .card--back { top: 480px; }

  /* Front */
  .front-brand {
    position: absolute; top: 118px; left: 0; width: 100%;
    display: flex; align-items: center; justify-content: center; gap: 18px;
  }
  .brand-dot {
    width: 56px; height: 56px; border-radius: 50%;
    background: var(--brand-sky);
  }
  .brand-name {
    font-weight: 400; font-size: 40px; color: var(--ink-dark);
    letter-spacing: 0.5px;
  }
  .tagline {
    position: absolute; top: 262px; width: 100%; text-align: center;
    font-size: 15px; color: var(--ink-grey); letter-spacing: 0.3px;
  }

  /* Back */
  .back-band {
    position: absolute; left: 0; top: 96px; width: 100%; height: 258px;
    background: var(--brand-blue);
  }
  .back-dot {
    position: absolute; left: 54px; top: 36px;
    width: 128px; height: 128px; border-radius: 50%;
    background: var(--brand-sky); border: 5px solid var(--card-white);
  }
  .back-brand {
    position: absolute; left: 40px; top: 232px;
    font-size: 36px; font-weight: 400; color: var(--ink-dark);
  }
  .back-divider {
    position: absolute; left: 318px; top: 132px; width: 1px; height: 190px;
    background: var(--divider);
  }
  .contact {
    position: absolute; left: 336px; top: 128px; width: 270px;
    color: var(--on-blue);
  }
  .contact__name { font-weight: 700; font-size: 17px; letter-spacing: 0.4px; text-transform: uppercase; }
  .contact__role { font-size: 13px; text-transform: uppercase; letter-spacing: 0.3px; margin-top: 1px; }
  .contact__quals { font-size: 10.5px; line-height: 1.4; margin-top: 3px; }
  .contact__list { list-style: none; margin-top: 12px; }
  .contact__item {
    display: flex; align-items: center; gap: 9px;
    font-size: 13px; line-height: 1; margin-bottom: 7px;
  }
  .contact__icon { width: 13px; height: 13px; flex: none; }
</style>
</head>
<body>
<main class="stage">

  <section class="card card--front" aria-label="Card front">
    <div class="front-brand">
      <span class="brand-dot"></span>
      <span class="brand-name">Thrive Lane</span>
    </div>
    <p class="tagline">Caring For Your Psychological Well-Being Is Our Top Priority</p>
  </section>

  <section class="card card--back" aria-label="Card back">
    <div class="back-band"></div>
    <span class="back-dot"></span>
    <span class="back-brand">Thrive Lane</span>
    <div class="back-divider"></div>
    <div class="contact">
      <p class="contact__name">Dara Whelby</p>
      <p class="contact__role">Counsellor &amp; Psychotherapist</p>
      <p class="contact__quals">BSc (Psychol.), BA, Dip. (Couns. &amp; Psych.)<br>PG.Cert (CBT), FGTrK, ONRE</p>
      <ul class="contact__list">
        <li class="contact__item">
          <svg class="contact__icon" viewBox="0 0 13 13" aria-hidden="true"><rect x="3" y="0.5" width="7" height="12" rx="1.3" fill="none" stroke="#fff" stroke-width="1.3"/><circle cx="6.5" cy="10.2" r="0.8" fill="#fff"/></svg>
          555 204 7781
        </li>
        <li class="contact__item">
          <svg class="contact__icon" viewBox="0 0 13 13" aria-hidden="true"><rect x="0.5" y="2.5" width="12" height="8" fill="#fff"/><path d="M0.8 2.8 L6.5 7.2 L12.2 2.8" fill="none" stroke="#45b3ec" stroke-width="1.1"/></svg>
          dara@thrivelane.com
        </li>
        <li class="contact__item">
          <svg class="contact__icon" viewBox="0 0 13 13" aria-hidden="true"><circle cx="6.5" cy="6.5" r="6" fill="none" stroke="#fff" stroke-width="1.2"/><ellipse cx="6.5" cy="6.5" rx="2.6" ry="6" fill="none" stroke="#fff" stroke-width="1"/><line x1="0.5" y1="6.5" x2="12.5" y2="6.5" stroke="#fff" stroke-width="1"/></svg>
          www.thrivelane.com
        </li>
      </ul>
    </div>
  </section>

</main>
</body>
</html>
```